Revamp Of Landing Page For an Automated AI Voice Agents Agency

here is my current landing page https://app.brightfernpromotionhub.biz/v2/preview/WXKRPmQ4hLzYBvNdTeGS?notrack=true

Please use all my current content and imagery of ai agents in your new design. Make it easy to ready, easy to navigate and easy to understand

I am looking for a SLEEK shiny polished looking website. I like Dark themed sites but am open to see light themed sites too so please dont be shy.

The site should have an Ai Voice Agent Theme about it. Maybe look and feel of futureistic but simple and not intimidating to the average person...

Here are a couple website designs I like for reference:
https://q7v.io/
https://ai-bots.marekholvin.com/
https://chatwelmo.com/ai-agents

Target Market(s)

b2b

Industry/Entity Type

AI Voice Agents

Coding

Coded - Design and coding required

Font styles to use
Other font styles liked:
• open

Requirements
Must have
• all elements and content and images used in existing design.
Nice to have
• open
Should not have
• open

```html
<!DOCTYPE html>
<html lang="en">
<head>
<meta charset="utf-8">
<title>Callvera – AI Voice Agents</title>
<link href="https://fonts.googleapis.com/css2?family=Figtree:ital,wght@0,400;0,500;0,600;0,700;1,600;1,700&display=swap" rel="stylesheet">
<style>
:root{
  --page:#000;
  --navy:#0b0828;
  --navy-2:#140d3a;
  --card:#0b0a17;
  --card-line:#2e2b42;
  --white:#fff;
  --muted:#b9b6cc;
  --soft:#d8d6e6;
  --violet:#7b5cf6;
  --violet-2:#8f55ef;
  --indigo:#4f46e5;
  --track:#2a2740;
}
*{box-sizing:border-box;margin:0;padding:0}
html,body{width:1200px;height:3228px;overflow:hidden;background:var(--page)}
body{font-family:"Figtree",sans-serif;color:var(--white);position:relative}
.page{position:absolute;left:69px;top:55px;width:710px}
section,.bottom-bar{position:relative;overflow:hidden}
.abs{position:absolute}
.accent{color:var(--violet)}
.btn{position:absolute;display:flex;align-items:center;justify-content:center;background:linear-gradient(90deg,var(--indigo),var(--violet-2));color:var(--white);font-weight:700;font-size:12px;border-radius:2px;text-decoration:none}
.note{position:absolute;left:0;width:710px;text-align:center;font-style:italic;font-weight:600;font-size:9.5px;line-height:12px;color:var(--soft)}
.photo{position:absolute;border-radius:8px}
.dots{background-image:radial-gradient(rgba(140,130,220,.18) 1px,transparent 1.2px);background-size:7px 7px}

/* hero */
.hero{height:390px;background:linear-gradient(180deg,#0d0930,#0f0a33)}
.logo{left:25px;top:34px;display:flex;align-items:center;gap:6px;font-weight:600;font-size:13px;letter-spacing:1.5px}
.logo i{width:9px;height:9px;border:1.5px solid var(--white);border-radius:50%}
.hero h1{left:25px;top:95px;font-size:25px;line-height:29px;font-weight:700}
.checks{left:25px;top:166px;display:grid;grid-template-columns:115px 150px;row-gap:5px;font-size:10px;color:var(--soft)}
.checks li{list-style:none;display:flex;align-items:center;gap:5px}
.checks li:nth-child(5){grid-column:1}
.tick{width:10px;height:10px;border-radius:50%;background:#9a98ac;display:inline-flex;align-items:center;justify-content:center}
.hero p{left:25px;top:294px;width:270px;font-size:9px;line-height:11.5px;color:var(--soft)}

/* agent cards */
.agent{position:absolute;width:323px;height:178px;background:var(--card);border:1px solid var(--card-line);border-radius:6px}
.agent .photo{left:9px;top:9px;width:112px;height:159px;border-radius:5px}
.agent .head{position:absolute;left:136px;top:16px;right:10px;display:flex;align-items:center;gap:8px;font-size:15.5px;font-weight:600;line-height:18px}
.badge{width:38px;height:38px;flex:none;border-radius:50%;display:flex;align-items:center;justify-content:center}
.agent .lead{position:absolute;left:136px;right:10px;font-size:9px;line-height:11px;font-weight:700}
.agent .desc{position:absolute;left:136px;right:10px;font-size:8.6px;line-height:10.6px;color:var(--muted)}

.meet{height:476px;background:linear-gradient(180deg,#0c0a24,#090818)}
.section-title{position:absolute;left:0;width:710px;text-align:center;font-weight:700}
.progress{left:25px;top:308px;width:660px;height:4px;background:var(--track)}
.progress b{display:block;width:265px;height:4px;background:linear-gradient(90deg,var(--indigo),var(--violet-2))}

/* install */
.install{height:319px;background:radial-gradient(ellipse at 50% 50%,#1d1250,#100a33 70%)}
.install h2{left:50px;top:76px;font-size:24px;line-height:26px;font-weight:700}
.install h3{left:50px;top:150px;font-size:14px;font-weight:700}
.install p{left:50px;top:169px;width:268px;font-size:9.8px;line-height:12.3px;color:var(--muted)}

/* why */
.why{height:363px;background:linear-gradient(180deg,#0b0920,#0a0818)}
.why-card{position:absolute;top:85px;height:116px;background:var(--card);border:1px solid var(--card-line);border-radius:5px;text-align:center;padding-top:10px}
.why-card svg{display:block;margin:0 auto 4px}
.why-card h4{font-size:14px;font-weight:700;line-height:16px}
.why-card p{font-size:8.8px;line-height:11px;color:var(--muted);margin-top:4px;padding:0 8px}

/* promise */
.promise{height:364px;background:radial-gradient(ellipse at 60% 50%,#1c1150,#0f0a34 75%)}
.promise h2{left:334px;top:95px;font-size:24px;font-weight:700}
.pledge{position:absolute;left:334px;background:rgba(10,8,30,.6);border:1px solid #4a4070;display:flex;align-items:center;gap:8px;padding:0 10px}
.pledge strong{font-size:15px;font-weight:600}
.pledge span{display:block;font-size:11px;color:var(--muted);line-height:13px}

/* reviews */
.reviews{height:375px;background:linear-gradient(180deg,#0d0a26,#0a0818)}
.reviews h2{font-size:25px;line-height:30px}
.review{position:absolute;top:150px;width:207px;height:157px;background:var(--card);border:1px solid var(--card-line);border-radius:5px;padding:8px 10px}
.stars{color:var(--violet);font-size:11px;letter-spacing:2px}
.review p{margin-top:4px;font-size:8.6px;line-height:11px;color:var(--muted)}
.review p b{color:var(--white)}
.who{position:absolute;left:10px;bottom:10px;display:flex;align-items:center;gap:6px}
.avatar{width:32px;height:32px;border-radius:50%}
.who strong{display:block;font-size:9px;font-weight:600}
.who span{font-size:7px;color:var(--muted)}
.pager{left:337px;top:324px;display:flex;gap:4px}
.pager i{width:6px;height:6px;border-radius:50%;background:#6e6a88}
.pager i:first-child{background:transparent;border:1px solid var(--white)}

/* faq */
.faq{height:407px;background:linear-gradient(180deg,#0a0818,#150d40)}
.qa{position:absolute;left:174px;width:362px;border:1px solid #6b4fc0;border-radius:4px;text-align:center;background:rgba(10,8,30,.5)}
.qa h4{font-size:15px;font-weight:600;margin-bottom:5px}
.qa p{font-size:11px;line-height:14px;color:var(--muted)}

/* closing */
.closing{height:370px;background:radial-gradient(ellipse at 40% 0%,#5a2a9a 0%,#2a1460 35%,#110b30 75%)}
.foot-col{position:absolute;top:282px;font-size:8px;line-height:11px;color:var(--muted)}
.foot-col h5{font-size:9px;color:var(--white);font-weight:600;margin-bottom:5px}
.bottom-bar{height:56px;background:#0e0a2c;border-top:1px solid #241d4d}
.bottom-bar small{position:absolute;left:50px;top:22px;font-size:8px;color:var(--soft)}
.socials{position:absolute;right:50px;top:20px;display:flex;gap:8px}
.socials i{width:14px;height:14px;border-radius:3px;background:#8a87a0}

.side{position:absolute;left:808px}
</style>
</head>
<body>

<main class="page">

<section class="hero">
  <div class="abs logo"><span>CALLVERA</span><i></i></div>
  <a class="btn" style="left:513px;top:23px;width:172px;height:36px">Get An Instant Free Demo</a>
  <h1 class="abs">AI Voice Agents That Work<br><span class="accent">24 Hours 7 Days A Week!</span></h1>
  <ul class="abs checks">
    <li><span class="tick"></span>Answering Calls</li>
    <li><span class="tick"></span>Send Emails &amp; Text Messages</li>
    <li><span class="tick"></span>Book Appointments</li>
    <li><span class="tick"></span>Follow Up Reminders</li>
    <li><span class="tick"></span>Transfer Calls &amp; More</li>
  </ul>
  <a class="btn" style="left:25px;top:238px;width:172px;height:38px">Get An Instant Free Demo</a>
  <p class="abs">We'll create a custom AI agent for your business at no cost. Click the button above — your new AI agent will call you in just a couple of minutes. Experience the magic and prepare to be impressed!</p>
  <div class="photo" role="img" aria-label="Two humanoid AI agents wearing headsets working at laptops in a bright office" style="left:362px;top:100px;width:323px;height:238px;background:linear-gradient(135deg,#8fb4c6,#d9e2e6 45%,#a98a7a 75%,#6d8796)"></div>
</section>

<section class="meet dots">
  <h2 class="section-title" style="top:44px;font-size:24px;line-height:26px">Meet Your New<br><span class="accent">AI-Powered Workforce</span></h2>

  <article class="agent" style="left:25px;top:110px">
    <div class="photo" role="img" aria-label="Smiling female AI receptionist android with headset" style="background:linear-gradient(160deg,#3b9fb0,#a8dadf 50%,#c7835e)"></div>
    <div class="head"><span class="badge" style="background:#1e9a6a"><svg width="18" height="18" viewBox="0 0 18 18" fill="none" stroke="#fff" stroke-width="1.6"><path d="M3 10a6 6 0 0 1 12 0"/><rect x="2" y="10" width="3" height="5" rx="1"/><rect x="13" y="10" width="3" height="5" rx="1"/></svg></span>AI Receptionist</div>
    <p class="lead" style="top:65px">Takes overflow and after-hours calls, or handles calls 24/7 &amp; transfers to the appropriate department.</p>
    <p class="desc" style="top:106px">Ava handles all your calls 24/7. She can also be set to only manage overflow or after-hours calls. Ava sends emails, SMS messages, and even books appointments during calls.</p>
  </article>

  <article class="agent" style="left:362px;top:110px">
    <div class="photo" role="img" aria-label="AI sales agent with headset typing at a laptop beside a city window" style="background:linear-gradient(160deg,#c9d4da,#7b8c98 50%,#2b2f36)"></div>
    <div class="head" style="top:30px"><span class="badge" style="background:#2f6fe6"><svg width="20" height="20" viewBox="0 0 20 20" fill="none" stroke="#fff" stroke-width="1.5"><circle cx="10" cy="10" r="7.5"/><path d="M12.5 7.5c-.5-1-1.5-1.3-2.5-1.3-1.4 0-2.4.7-2.4 1.8 0 2.5 5 1.3 5 3.9 0 1.1-1 1.9-2.6 1.9-1.2 0-2.1-.5-2.6-1.3M10 5v10"/></svg></span>Ai Sales Agent</div>
    <p class="desc" style="top:84px">Brian will take your inbound sales calls. Will give all detailed information to the customer, answer questions in a normal conversational tone and can book sales appointments or transfer hot prospects to a human to close the sale.</p>
  </article>

  <div class="abs progress"><b></b></div>
  <a class="btn" style="left:218px;top:349px;width:274px;height:38px">Get An Instant Free Demo</a>
  <p class="note" style="top:395px">We Will Create An Ai Agent Customized For Your Business At No Cost.<br>Simply Click The Button Above And Your Very Own Ai Agent Will Be Calling You In<br>Just A Couple Minutes. Experience The Magic And Get Ready To Be Very Impressed!</p>
</section>

<section class="install">
  <h2 class="abs">Install The <span class="accent">Power Of AI</span><br>For Your Business</h2>
  <h3 class="abs">Your Wish Is Their Command</h3>
  <p class="abs">Welcome your newest employees — AI Voice Agents who never call in sick, never complain, and never take a break. From handling inbound calls to sending emails, booking appointments, and following up with leads, your AI team works around the clock to save you time and money.</p>
  <div class="photo" role="img" aria-label="Two smiling humanoid AI agents with headsets in an office" style="left:377px;top:51px;width:284px;height:217px;background:linear-gradient(135deg,#4f8fa5,#c9d6d9 45%,#b4816a 70%,#e8ecef)"></div>
</section>

<section class="why dots">
  <h2 class="section-title" style="top:44px;font-size:24px">Why Businesses Love <span class="accent">AI Voice Agents</span></h2>
  <div class="why-card" style="left:25px;width:148px">
    <svg width="32" height="32" viewBox="0 0 32 32" fill="none" stroke="#7b5cf6" stroke-width="1.4"><path d="M25 7c-6 0-11 4-13 10l3 3c6-2 10-7 10-13z"/><circle cx="19" cy="13" r="2"/><path d="M12 17l-4 0 3-4 4 0M15 20v4l4-3v-4M9 23l-3 3"/></svg>
    <h4>Trained in Seconds</h4><p>Learns Your Entire Website In Seconds</p>
  </div>
  <div class="why-card" style="left:189px;width:153px">
    <svg width="34" height="34" viewBox="0 0 34 34" fill="none" stroke="#7b5cf6" stroke-width="1.4"><circle cx="17" cy="17" r="13"/><ellipse cx="17" cy="17" rx="6" ry="13"/><path d="M4 17h26M6 10h22M6 24h22"/></svg>
    <h4 style="margin-top:4px">Worldwide</h4><p>Works Anywhere In The Globe</p>
  </div>
  <div class="why-card" style="left:359px;width:141px">
    <svg width="30" height="32" viewBox="0 0 30 32" fill="none" stroke="#7b5cf6" stroke-width="1.4"><circle cx="15" cy="10" r="6"/><path d="M4 30c0-7 5-11 11-11s11 4 11 11M8 10a7 7 0 0 1 14 0"/></svg>
    <h4>User-friendly</h4><p>Your Ai Agents Sound As If They're Real Humans</p>
  </div>
  <div class="why-card" style="left:517px;width:168px">
    <svg width="32" height="32" viewBox="0 0 32 32" fill="none" stroke="#7b5cf6" stroke-width="1.4"><path d="M19 3L8 18h8l-3 11 11-15h-8z"/><path d="M4 6l3 3M27 5l-2 3M28 22l-3-1" stroke-dasharray="2 2"/></svg>
    <h4>Lightning-Fast<br>Responses</h4><p>Instant answers, no coffee, bathroom or lunch breaks needed</p>
  </div>
  <a class="btn" style="left:218px;top:234px;width:274px;height:38px">Get An Instant Free Demo</a>
  <p class="note" style="top:281px">We Will Create An Ai Agent Customized For Your Business At No Cost.<br>Simply Click The Button Above And Your Very Own Ai Agent Will Be Calling You In<br>Just A Couple Minutes. Experience The Magic And Get Ready To Be Very Impressed!</p>
</section>

<section class="promise">
  <div class="photo" role="img" aria-label="Smiling male AI agent with headset and a female AI agent behind him" style="left:99px;top:50px;width:200px;height:264px;border-radius:3px;background:linear-gradient(150deg,#3f8aa0,#d6dde0 45%,#a6745d 65%,#e6e9eb)"></div>
  <h2 class="abs">Our <span class="accent">Promise</span> To You</h2>
  <div class="pledge" style="top:139px;width:277px;height:49px">
    <svg width="30" height="30" viewBox="0 0 30 30" fill="none" stroke="#8f7cf0" stroke-width="1.4"><circle cx="15" cy="15" r="12" stroke-dasharray="3 2"/><circle cx="15" cy="15" r="8.5"/><path d="M17.5 12c-.5-.8-1.3-1.1-2.5-1.1-1.3 0-2.2.6-2.2 1.6 0 2.3 4.8 1.2 4.8 3.6 0 1-1 1.7-2.5 1.7-1.1 0-2-.4-2.5-1.2M15 9v12"/></svg>
    <strong>14-day money-back guarantee</strong>
  </div>
  <div class="pledge" style="top:198px;width:224px;height:63px">
    <svg width="28" height="30" viewBox="0 0 28 30" fill="none" stroke="#8f7cf0" stroke-width="1.4"><circle cx="14" cy="10" r="5"/><path d="M6 10a8 8 0 0 1 16 0M4 28c0-6 4-10 10-10s10 4 10 10"/><rect x="4" y="9" width="3" height="5" rx="1"/><rect x="21" y="9" width="3" height="5" rx="1"/></svg>
    <div><strong>24/7 Customer Support</strong><span>Often praised for our friendly<br>&amp; helpful support team</span></div>
  </div>
</section>

<section class="reviews dots">
  <h2 class="section-title" style="top:40px">After Our Customers Have A Conversation<br>With Their New Ai Voice Agent<br><span class="accent">They Give Us 5 Stars!</span></h2>
  <article class="review" style="left:25px">
    <div class="stars">★★★★★</div>
    <p>Before using this, I was drowning in missed calls and follow-ups. Now, everything just runs. Clients are getting booked, messages go out automatically — <b>it feels like my business finally has structure.</b></p>
    <div class="who"><div class="avatar" role="img" aria-label="Customer portrait" style="background:linear-gradient(135deg,#5a4ad6,#c59a7c)"></div><div><strong>Dean Harlow</strong><span>CEO, Fernbrook Landscaping</span></div></div>
  </article>
  <article class="review" style="left:252px">
    <div class="stars">★★★★★</div>
    <p><b>It's like I suddenly got a super-reliable assistant who never forgets a thing.</b> My calendar stays full, no one slips through the cracks, and I've got more time to actually grow the business.</p>
    <div class="who"><div class="avatar" role="img" aria-label="Customer portrait" style="background:linear-gradient(135deg,#5a4ad6,#d8b48a)"></div><div><strong>Nora Whitcombe</strong><span>CEO of Larkspur Strategies</span></div></div>
  </article>
  <article class="review" style="left:478px">
    <div class="stars">★★★★★</div>
    <p>What used to take three people and constant oversight now happens on autopilot. Calls get handled, leads get qualified, and I can focus on closing deals. <b>Best decision I've made all year.</b></p>
    <div class="who"><div class="avatar" role="img" aria-label="Customer portrait" style="background:linear-gradient(135deg,#5a4ad6,#d9823a)"></div><div><strong>Theo Brandt</strong><span>CEO of Brandt Consulting Group</span></div></div>
  </article>
  <div class="abs pager"><i></i><i></i><i></i><i></i></div>
</section>

<section class="faq">
  <h2 class="section-title" style="top:44px;font-size:24px">Do You Have Questions?</h2>
  <div class="qa" style="top:89px;height:88px;padding-top:10px">
    <h4>What exactly are the AI Voice Agents?</h4>
    <p>AI Voice Agents are specialized human sounding bots, having smart and masterful conversations and each is expertly trained in seconds for a specific business function.</p>
  </div>
  <div class="qa" style="top:193px;height:76px;padding-top:10px">
    <h4>How will these AI Voice Agents benefit</h4>
    <p>Ai Voice Agents Answer Calls, Book Appts, Send Emails,<br>Text Messages, Follow Up Reminders &amp; More For You 24/7!</p>
  </div>
  <div class="qa" style="top:283px;height:76px;padding-top:10px">
    <h4>Are they easy to use?</h4>
    <p>We provide a done for you service. We create your<br>AI Voice Agent and launch it within days!</p>
  </div>
</section>

<section class="closing">
  <h2 class="section-title" style="top:48px;font-size:24px;line-height:29px">These AI Agents Can Help Your Business<br>Tremendously. Imagine The Possibilities.</h2>
  <a class="btn" style="left:218px;top:129px;width:274px;height:38px">Get An Instant Free Demo</a>
  <p class="note" style="top:173px">We Will Create An Ai Agent Customized For Your Business At No Cost.<br>Simply Click The Button Above And Your Very Own Ai Agent Will Be Calling You In<br>Just A Couple Minutes. Experience The Magic And Get Ready To Be Very Impressed!</p>
  <div class="foot-col" style="left:50px;width:185px"><h5>*14-Day Money Back Guarantee Terms:</h5>If you use the ai agents and you're not happy. Then you can contact us in the first 14 days for a full refund.</div>
  <div class="foot-col" style="left:294px"><h5>Legal</h5>Privacy<br>Terms and Conditions<br>Earnings &amp; Product Disclaimer</div>
  <div class="foot-col" style="left:480px;width:200px"><h5>Contact</h5>Do you have questions about Callvera.<br>Please email info@callvera-agents.com.</div>
</section>

<footer class="bottom-bar">
  <small>© 2025 Callvera. All Rights Reserved.</small>
  <div class="socials"><i></i><i></i><i></i></div>
</footer>

</main>

<aside>
  <article class="agent side" style="top:555px">
    <div class="photo" role="img" aria-label="AI lead qualifier with headset in a dark city office" style="background:linear-gradient(160deg,#1b2d50,#3a6a9a 50%,#101828)"></div>
    <div class="head"><span class="badge" style="background:#e5505a"><svg width="18" height="18" viewBox="0 0 18 18" fill="none" stroke="#fff" stroke-width="1.5"><rect x="3" y="2" width="10" height="13" rx="1"/><circle cx="13" cy="13" r="3"/><path d="M6 6h4M6 9h3"/></svg></span>Ai Lead Qualifier</div>
    <p class="lead" style="top:65px">Conversate With Prospects To Qualify Before Handing Over To Sales Team</p>
    <p class="desc" style="top:94px">All of our ai agents gather information and qualify leads. If they are interested in the services on the call then our ai agents will assist them with booking an appointment with our sales team over the call.</p>
  </article>
  <article class="agent side" style="top:757px">
    <div class="photo" role="img" aria-label="Female AI follow-up agent android with headset" style="background:linear-gradient(160deg,#2a6f86,#b7d3da 50%,#3a3040)"></div>
    <div class="head" style="top:26px"><span class="badge" style="background:#8a55d6"><svg width="18" height="18" viewBox="0 0 18 18" fill="none" stroke="#fff" stroke-width="1.5"><rect x="3" y="2" width="10" height="14" rx="1"/><path d="M6 6h4M6 9h4M6 12h2"/></svg></span>Ai Follow Up<br>Reminders</div>
    <p class="lead" style="top:90px">Calls, Sends SMS &amp; Email Reminders</p>
    <p class="desc" style="top:106px">Sophia handles all the follow up calls, appointment reminders and sends out the email and sms reminders too.</p>
  </article>
  <article class="agent side" style="top:958px">
    <div class="photo" role="img" aria-label="AI appointment setter with headset typing on a keyboard" style="background:linear-gradient(160deg,#5a8ea4,#d1dde2 50%,#7a8c96)"></div>
    <div class="head" style="top:26px"><span class="badge" style="background:#f0a020"><svg width="18" height="18" viewBox="0 0 18 18" fill="none" stroke="#fff" stroke-width="1.5"><rect x="2" y="4" width="12" height="11" rx="1"/><path d="M2 8h12M5 2v3M11 2v3"/><circle cx="14" cy="13" r="3"/></svg></span>Ai Appointment<br>Setter</div>
    <p class="lead" style="top:78px">Book Appointments &amp; Reservations On Auto Pilot</p>
    <p class="desc" style="top:106px">Lily offers business advice, helps brainstorm ideas, and provides insights on growth tactics to support your entrepreneurial journey.</p>
  </article>
</aside>

</body>
</html>
```